Visit card

Industry/Entity Type

Health Care

Contact Information for Business Card

O VITALIS SYSTEMS
Odile Brevard - chef de Projet

Requirements
Must have
• 318 Gaston Lemaire Street 59710 LORVANNE Tel: 33 (0) 327 481 605 Mobile: 06 42 19 37 64 Web: www.quorvexsystems.example Contact: o.brevard@o-vitalissystems.example
Should not have
• Respect for color

```html
<!DOCTYPE html>
<html lang="fr">
<head>
<meta charset="utf-8">
<title>O Vitalis Systems – Carte de visite</title>
<link href="https://fonts.googleapis.com/css2?family=Lato:wght@400;700;900&display=swap" rel="stylesheet">
<style>
  :root {
    --backdrop: #2b2b2b;
    --card: #232323;
    --ink: #f2f2f2;
    --silver: #b9b9b9;
    --accent: #e3202b;
  }
  * { box-sizing: border-box; margin: 0; padding: 0; }
  html, body { width: 1200px; height: 900px; overflow: hidden; }
  body {
    background: var(--backdrop);
    font-family: "Lato", sans-serif;
    color: var(--ink);
    position: relative;
  }
  .card {
    position: absolute;
    left: 250px;
    width: 700px;
    height: 400px;
    background: var(--card);
    overflow: hidden;
  }
  .card--front { top: 30px; }
  .card--back { top: 470px; }

  .brand {
    position: absolute;
    display: flex;
    align-items: center;
    gap: 22px;
  }
  .brand__dot {
    border-radius: 50%;
    flex: none;
  }
  .brand__name {
    font-weight: 900;
    letter-spacing: 0.04em;
    line-height: 1;
  }

  .card--front .brand { left: 0; right: 0; top: 150px; justify-content: center; }
  .card--front .brand__dot { width: 96px; height: 96px; background: #161616; }
  .card--front .brand__name { font-size: 44px; color: var(--silver); }

  .card--back .brand { left: 36px; top: 166px; gap: 16px; }
  .card--back .brand__dot { width: 66px; height: 66px; background: var(--ink); }
  .card--back .brand__name { font-size: 24px; color: var(--ink); width: 170px; }

  .divider {
    position: absolute;
    left: 330px;
    top: 80px;
    width: 2px;
    height: 250px;
    background: var(--ink);
  }

  .contact {
    position: absolute;
    left: 360px;
    top: 70px;
    width: 330px;
  }
  .contact__name {
    color: var(--accent);
    font-weight: 700;
    font-size: 22px;
    letter-spacing: 0.03em;
    text-transform: uppercase;
  }
  .contact__role { font-size: 17px; margin-top: 2px; }
  .contact__address { font-size: 17px; line-height: 1.3; margin-top: 18px; }
  .contact__list { list-style: none; margin-top: 16px; }
  .contact__item {
    display: flex;
    align-items: center;
    gap: 12px;
    font-size: 17px;
    line-height: 1.75;
    white-space: nowrap;
  }
  .contact__item svg { width: 16px; height: 16px; flex: none; fill: var(--accent); }

  .edge {
    position: absolute;
    left: 0; right: 0; bottom: 0;
    height: 8px;
    background: var(--accent);
  }
</style>
</head>
<body>

<section class="card card--front" aria-label="Recto">
  <div class="brand">
    <span class="brand__dot"></span>
    <span class="brand__name">O VITALIS SYSTEMS</span>
  </div>
</section>

<section class="card card--back" aria-label="Verso">
  <div class="brand">
    <span class="brand__dot"></span>
    <span class="brand__name">O VITALIS SYSTEMS</span>
  </div>

  <div class="divider"></div>

  <div class="contact">
    <p class="contact__name">Odile Brevard</p>
    <p class="contact__role">Chef de Projet</p>
    <p class="contact__address">318 Rue Gaston Lemaire<br>59710 LORVANNE</p>
    <ul class="contact__list">
      <li class="contact__item">
        <svg viewBox="0 0 16 16" aria-hidden="true"><path d="M4 0h8a1 1 0 0 1 1 1v14a1 1 0 0 1-1 1H4a1 1 0 0 1-1-1V1a1 1 0 0 1 1-1zm1 2v10h6V2zm3 11a1 1 0 1 0 0 2 1 1 0 0 0 0-2z"/></svg>
        06 42 19 37 64
      </li>
      <li class="contact__item">
        <svg viewBox="0 0 16 16" aria-hidden="true"><path d="M3.6 1l2.6 3-1.6 1.8a9 9 0 0 0 5.6 5.6L12 9.8l3 2.6-1.4 2.4C7.4 15.2.8 8.6 1.2 2.4z"/></svg>
        +33 (0) 327 481 605
      </li>
      <li class="contact__item">
        <svg viewBox="0 0 16 16" aria-hidden="true"><path d="M1 3h14v1.2L8 8.6 1 4.2zm0 2.6l7 4.4 7-4.4V13H1z"/></svg>
        o.brevard@o-vitalissystems.example
      </li>
      <li class="contact__item">
        <svg viewBox="0 0 16 16" aria-hidden="true"><path d="M8 0a8 8 0 1 0 0 16A8 8 0 0 0 8 0zm0 1.5c.9 0 1.9 1.8 2.2 4.5H5.8C6.1 3.3 7.1 1.5 8 1.5zM1.6 7h2.9a14 14 0 0 0 0 2H1.6a6.5 6.5 0 0 1 0-2zm4.2 0h4.4a13 13 0 0 1 0 2H5.8a13 13 0 0 1 0-2zm5.7 0h2.9a6.5 6.5 0 0 1 0 2h-2.9a14 14 0 0 0 0-2zM5.8 10h4.4c-.3 2.7-1.3 4.5-2.2 4.5s-1.9-1.8-2.2-4.5z"/></svg>
        www.quorvexsystems.example
      </li>
    </ul>
  </div>

  <div class="edge"></div>
</section>

</body>
</html>
```